Harrowmere Freight, Project

Company Profile
Harrowmere Freight Sdn Bhd is a well established and experienced freight forwarder in Kuala Lumpur, Malaysia. We specialize in air and sea forwarding, Custom Brokerage and regulatory compliance services, inland transportation,
overseas freighting and warehousing and distribution management. With our dedicated qualified and experienced professionals, we are fully committed to serving our clients.

Our Mission
Based on the motto “Quick, Reliable and Polite”, Harrowmere Freight is dedicated to upholding the following three points corporate philosophy:
1. Adhering to the principle that “the customer always comes first”.
2. Contributing to the development of the local community.
3. Making it our duty to be responsible and sincere.

Our Edge
• One-Stop Logistics Solutions
• Extensive Network Throughout Malaysia
• Highly Qualified and Experienced Pool of Professionals
• Comprehensive IT Solutions
• Innovative and Customer-focused Solutions
• Flexible and Consistent in Managing Exceptions
• Total Supply Chain Visibility

Target Market(s)

We sell the logistics services to all the industry in Malaysia. (ONE Stop Logistics Solutions)

Industry/Entity Type

Logistic

Contact Information for Business Card

I want the back of the card to be white with the logo and slogan. i would like to see the logo on the front with the general info.

Requirements
Must have
• Name, Title, Office, Cell, Fax, Email, Address, Website
Nice to have
• Modern Design Business Card

```html
<!DOCTYPE html>
<html lang="en">
<head>
<meta charset="utf-8">
<title>Harrowmere Freight — Stationery Set</title>
<link href="https://fonts.googleapis.com/css2?family=Montserrat:wght@400;500;600;700&family=Arimo:wght@400;700&display=swap" rel="stylesheet">
<style>
  :root{
    --backdrop:#e3e3e5;
    --paper:#ffffff;
    --blue:#2590d6;
    --blue-light:#28abe3;
    --blue-deep:#1a74ba;
    --charcoal:#555557;
    --ink:#1e1e20;
    --muted:#6b6b6e;
    --faint:#eef3f8;
  }
  *{box-sizing:border-box;margin:0;padding:0}
  html,body{width:1189px;height:1200px;overflow:hidden;background:var(--backdrop)}
  body{position:relative;font-family:"Montserrat",Arial,sans-serif;color:var(--ink)}
  .sheet{position:absolute;background:var(--paper);overflow:hidden}

  /* brand name used in place of a mark */
  .brand-name{font-family:"Montserrat",Arial,sans-serif;font-weight:600;color:var(--charcoal);line-height:1.05}
  .tagline{font-family:"Montserrat",Arial,sans-serif;color:var(--blue);letter-spacing:.12em}

  /* letterhead */
  .letterhead{left:50px;top:110px;width:508px;height:657px}
  .letterhead .brand{position:absolute;left:52px;top:76px;width:135px;text-align:center}
  .letterhead .brand .brand-name{font-size:19px}
  .letterhead .brand .tagline{font-size:7px;margin-top:6px}
  .letterhead .sender{position:absolute;right:59px;top:42px;text-align:right;font-size:7.5px;color:#444;line-height:1.35}
  .letterhead .sender h1{font-size:13px;font-weight:500;color:#333;letter-spacing:.01em;line-height:1.1}
  .letterhead .sender .reg-no{font-size:6px;margin-bottom:6px}
  .letterhead .sender .address{margin-bottom:4px}
  .contact-line{display:flex;justify-content:flex-end;align-items:center;gap:3px}
  .icon{display:inline-block;width:7px;height:7px;background:var(--blue);border-radius:1px;flex:none}
  .letterhead .sender .gst{font-weight:700;font-size:6.5px;margin-top:5px;color:#222}

  .letter{position:absolute;left:55px;top:187px;width:392px;font-family:"Arimo",Arial,sans-serif;font-size:9.4px;line-height:14.9px;color:#222}
  .letter .recipient{margin-bottom:38px}
  .letter .recipient strong{display:block;font-size:10px;margin-bottom:6px;line-height:12px}
  .letter .recipient span{display:block;line-height:11px}
  .letter p{margin-bottom:15px;text-align:justify}
  .letter .regards{margin-top:27px}
  .signature{display:block;width:120px;height:36px;margin:6px 0 5px;background:linear-gradient(90deg,#f2f2f4,#fafafa);border-radius:3px}
  .letter .signatory strong{display:block;font-size:10px;line-height:12px}
  .letter .signatory span{line-height:12px}

  .footer-band{position:absolute;left:0;bottom:0;width:100%;height:21px}

  /* folder */
  .folder{left:629px;top:111px;width:506px;height:654px;background:linear-gradient(180deg,var(--blue-light) 0%,var(--blue-deep) 100%)}
  .folder .brand{position:absolute;left:0;right:0;top:355px;text-align:center}
  .folder .brand-name{color:#fff;font-size:28px}

  /* envelopes */
  .envelope-front{left:47px;top:849px;width:401px;height:201px;box-shadow:0 0 0 1px #d9d9db}
  .envelope-front .brand{position:absolute;left:16px;top:52px;width:80px;text-align:center}
  .envelope-front .brand .brand-name{font-size:11px}
  .envelope-front .brand .tagline{font-size:4.3px;margin-top:3px}
  .envelope-front .sender{position:absolute;right:16px;top:23px;text-align:right;font-size:5.8px;font-weight:700;color:#333}
  .envelope-front .sender small{display:block;font-size:3.6px;font-weight:400;color:var(--blue)}
  .envelope-front .address{position:absolute;left:17px;top:154px;font-size:4.6px;line-height:6.2px;color:#444}

  .envelope-back{left:479px;top:849px;width:401px;height:201px;box-shadow:0 0 0 1px #d9d9db}
  .envelope-back .flap{position:absolute;left:0;top:0}
  .envelope-back .brand-name{position:absolute;left:0;right:0;top:20px;text-align:center;color:#fff;font-size:10px}

  /* business cards */
  .card{width:215px;height:122px;left:921px;box-shadow:0 0 0 1px #dcdcde}
  .card-front{top:805px}
  .card-front .brand{position:absolute;left:12px;top:20px;width:118px}
  .card-front .brand .brand-name{font-size:10.5px}
  .card-front .brand .tagline{font-size:4.3px;margin-top:3px}
  .card-front .person{position:absolute;right:10px;top:14px;text-align:right;font-size:5px;line-height:6px;color:#333}
  .card-front .person strong{display:block;font-size:6.8px;color:var(--blue);line-height:8px}
  .card-front .company{position:absolute;left:10px;top:69px;font-size:6.6px;font-weight:700;color:#222}
  .card-front .company small{display:block;font-size:3.8px;font-weight:400;color:var(--blue)}
  .card-front .contacts{position:absolute;left:10px;top:89px;font-size:4.8px;line-height:7.5px;color:#333}
  .card-front .contacts div{display:flex;align-items:center;gap:2px}
  .card-front .contacts .icon{width:5px;height:5px}
  .card-front .address{position:absolute;right:10px;top:74px;text-align:right;font-size:4.8px;line-height:6.5px;color:#333}
  .card-front .footer-band{height:8px}

  .card-back{top:953px}
  .card-back h2{position:absolute;left:11px;top:14px;font-size:6.8px;font-weight:700;color:var(--blue)}
  .card-back ul{position:absolute;left:11px;top:30px;list-style:none;font-size:4.9px;line-height:8.6px;color:#444}
  .card-back li{display:flex;align-items:center;gap:4px}
  .card-back li::before{content:"";width:4px;height:4px;background:var(--blue);opacity:.6;transform:rotate(45deg)}
  .card-back .brand{position:absolute;right:10px;top:95px;text-align:right}
  .card-back .brand .brand-name{font-size:8px}
  .card-back .slogan{position:absolute;left:11px;top:100px;font-size:5.4px;font-weight:500;color:var(--blue)}
  .card-back .info-bar{position:absolute;left:0;bottom:0;width:100%;height:11px;background:var(--blue);color:#fff;display:flex;justify-content:space-between;align-items:center;padding:0 8px 0 11px;font-size:4.6px}
  .card-back .info-bar small{font-size:3.6px}
</style>
</head>
<body>

<!-- Letterhead -->
<section class="sheet letterhead" aria-label="Letterhead">
  <div class="brand">
    <div class="brand-name">Harrowmere Freight</div>
    <div class="tagline">Quick, Reliable and Polite</div>
  </div>
  <header class="sender">
    <h1>HARROWMERE FREIGHT SDN. BHD</h1>
    <div class="reg-no">(Company No. 1264088-K)</div>
    <div class="address">No. 14B, 2nd Floor, Jalan Seroja Indah 3, Taman Seroja Jaya<br>41050 Klang, Selangor Darul Ehsan, Malaysia.</div>
    <div class="contact-line">(603) 3370 5216 <i class="icon"></i></div>
    <div class="contact-line">(603) 3370 5217 <i class="icon"></i></div>
    <div class="contact-line">enquiry@harrowmere.com.my <i class="icon"></i></div>
    <div class="gst">GST Registration No: 000418205976</div>
  </header>

  <article class="letter">
    <div class="recipient">
      <strong>JOHN SMITH</strong>
      <span>Street Name,City Name.</span>
      <span>Zip Coad 0000</span>
    </div>
    <p>Lorem Ipsum is simply dummy text of the printing and typesetting industry. Lorem Ipsum has been the industry's standard dummy text ever since the 1500s, when an unknown printer took a galley of type and scrambled it to make a type specimen book. It has survived not only five centuries, but also the leap into electronic typesetting, remaining essentially unchanged. It was popularised in the 1960s with the release of Letraset sheets containing Lorem Ipsum passages, and more recently with desktop publishing software like Aldus PageMaker including versions of Lorem Ipsum.</p>
    <p>It is a long established fact that a reader will be distracted by the readable content of a page when looking at its layout. The point of using Lorem Ipsum is that it has a more-or-less normal distribution of letters, as opposed to using 'Content here, content here', making it look like readable English. Many desktop publishing packages and web page editors now use Lorem Ipsum as their default model text, and a search for 'lorem ipsum' will uncover many web sites still in their infancy. Various versions have evolved over the years, sometimes by accident, sometimes on purpose (injected humour and the like).</p>
    <div class="regards">Regards,</div>
    <span class="signature" role="img" aria-label="Handwritten signature of John Doe"></span>
    <div class="signatory"><strong>John Doe</strong><span>General Maneger</span></div>
  </article>

  <svg class="footer-band" viewBox="0 0 508 21" preserveAspectRatio="none" aria-hidden="true">
    <polygon points="0,6 313,6 308,21 0,21" fill="var(--charcoal)"/>
    <polygon points="325,0 508,0 508,21 319,21" fill="var(--blue)"/>
  </svg>
</section>

<!-- Presentation folder -->
<section class="sheet folder" aria-label="Presentation folder">
  <div class="brand"><div class="brand-name">Harrowmere Freight</div></div>
</section>

<!-- DL envelope front -->
<section class="sheet envelope-front" aria-label="Envelope front">
  <div class="brand">
    <div class="brand-name">Harrowmere Freight</div>
    <div class="tagline">Quick, Reliable and Polite</div>
  </div>
  <div class="sender">HARROWMERE FREIGHT SDN. BHD.<small>(1264088-K)</small></div>
  <div class="address">No. 14B, 2nd Floor,<br>Jalan Seroja Indah 3,<br>Taman Seroja Jaya, 41050 Klang,<br>Selangor Darul Ehsan,<br>Malaysia.</div>
  <svg class="footer-band" style="height:11px" viewBox="0 0 401 11" preserveAspectRatio="none" aria-hidden="true">
    <polygon points="0,1 246,1 240,11 0,11" fill="#3a3a3c"/>
    <polygon points="252,0 401,0 401,11 245,11" fill="var(--blue)"/>
  </svg>
</section>

<!-- DL envelope back -->
<section class="sheet envelope-back" aria-label="Envelope back">
  <svg class="flap" width="401" height="58" viewBox="0 0 401 58" aria-hidden="true">
    <defs>
      <linearGradient id="flapFill" x1="0" y1="0" x2="0" y2="1">
        <stop offset="0" stop-color="var(--blue-light)"/>
        <stop offset="1" stop-color="var(--blue-deep)"/>
      </linearGradient>
    </defs>
    <path d="M0,0 H401 L392,50 Q390,57 382,57 H18 Q10,57 8,50 Z" fill="url(#flapFill)"/>
  </svg>
  <div class="brand-name">Harrowmere Freight</div>
</section>

<!-- Business card front -->
<section class="sheet card card-front" aria-label="Business card front">
  <div class="brand">
    <div class="brand-name">Harrowmere Freight</div>
    <div class="tagline">Quick, Reliable and Polite</div>
  </div>
  <div class="person"><strong>Farid Hakimi</strong>Managing Director<br>+6012-847 2093</div>
  <div class="company">HARROWMERE FREIGHT SDN. BHD.<small>(1264088-K)</small></div>
  <div class="contacts">
    <div><i class="icon"></i>(603) 3370 5215 / 5216</div>
    <div><i class="icon"></i>(603) 3370 5217</div>
    <div><i class="icon"></i>farid.hakimi@harrowmere.com.my</div>
  </div>
  <div class="address">No. 14B, 2nd Floor,<br>Jalan Seroja Indah 3,<br>Taman Seroja Jaya, 41050 Klang,<br>Selangor Darul Ehsan,<br>Malaysia.</div>
  <svg class="footer-band" viewBox="0 0 215 8" preserveAspectRatio="none" aria-hidden="true">
    <polygon points="0,1 132,1 129,8 0,8" fill="#3a3a3c"/>
    <polygon points="136,0 215,0 215,8 132,8" fill="var(--blue)"/>
  </svg>
</section>

<!-- Business card back -->
<section class="sheet card card-back" aria-label="Business card back">
  <h2>We're Specialize In</h2>
  <ul>
    <li>One-Stop Logistics Solutions</li>
    <li>Extensive Network Throughout Malaysia</li>
    <li>Highly Qualified and Experienced Pool of Professionals</li>
    <li>Comprehensive IT Solutions</li>
    <li>Innovative and Customer-focused Solutions</li>
    <li>Flexible and Consistent in Managing Exceptions</li>
    <li>Total Supply Chain Visibility</li>
  </ul>
  <div class="slogan">ONE STOP LOGISTICS SOLUTIONS</div>
  <div class="brand"><div class="brand-name">Harrowmere Freight</div></div>
  <div class="info-bar"><span>www.harrowmere.com.my</span><small>GST Registration No: 000418205976</small></div>
</section>

</body>
</html>
```